Lumavento business card

We need a modern business card - With our 4 colors - See web: www.lumavento.dk

I have attached logo and som old business Cards we have - Lets Make the new ones shine...:-) -

Industry/Entity Type

Business

Requirements
Must have
• the logo with lumavento only,

```html
<!DOCTYPE html>
<html lang="da">
<head>
<meta charset="utf-8">
<title>Lumavento – visitkort</title>
<link rel="stylesheet" href="https://fonts.googleapis.com/css2?family=Source+Sans+3:wght@400;600&display=swap">
<style>
  :root {
    --backdrop: #5a5a5a;
    --paper: #ffffff;
    --lime: #8dc75a;
    --plum: #6b2a75;
    --magenta: #c9358a;
    --tangerine: #e2873d;
    --ink: #1f1f1f;
    --ink-soft: #5b5b5b;
    --font: "Source Sans 3", "Myriad Pro", Arial, sans-serif;
  }
  * { box-sizing: border-box; margin: 0; padding: 0; }
  html, body {
    width: 1105px; height: 1200px; overflow: hidden;
    background: var(--backdrop);
    font-family: var(--font);
  }
  .card {
    position: absolute; left: 192px; width: 720px; height: 412px;
    background: var(--paper); overflow: hidden;
  }
  .card--front { top: 145px; }
  .card--back { top: 600px; }

  .stripes {
    position: absolute; left: 0; right: 0; bottom: 0;
    display: grid; grid-template-columns: 177fr 175fr 179fr 181fr;
    column-gap: 3px; background: var(--paper);
  }
  .card--front .stripes { height: 22px; }
  .card--back .stripes { top: 0; height: 100%; }
  .stripe--lime { background: var(--lime); }
  .stripe--plum { background: var(--plum); }
  .stripe--magenta { background: var(--magenta); }
  .stripe--tangerine { background: var(--tangerine); }

  /* front brand block */
  .brand-front { position: absolute; left: 106px; width: 275px; top: 176px; text-align: center; }
  .brand-dot {
    width: 34px; height: 34px; border-radius: 50%;
    background: var(--lime); margin: 0 auto 14px;
  }
  .wordmark { font-size: 27px; font-weight: 400; letter-spacing: 3px; line-height: 1; }
  .brand-front .wordmark { color: var(--ink); }
  .rule { height: 3px; margin-top: 16px; }
  .brand-front .rule { background: var(--lime); }
  .tagline { font-size: 17px; margin-top: 16px; }
  .brand-front .tagline { color: var(--ink); }

  /* front contact block */
  .contact { position: absolute; left: 407px; top: 82px; }
  .contact__name { color: var(--lime); font-size: 27px; font-weight: 600; line-height: 1.1; }
  .contact__role { color: var(--ink); font-size: 19px; margin-top: 2px; }
  .contact__address { color: var(--ink-soft); font-size: 18px; line-height: 29px; margin-top: 8px; font-style: normal; }
  .contact__list { list-style: none; margin-top: 8px; }
  .contact__item {
    display: flex; align-items: center; gap: 12px;
    color: var(--ink-soft); font-size: 18px; line-height: 28px;
  }
  .contact__icon { width: 16px; height: 16px; fill: var(--lime); flex: none; }

  /* back brand block */
  .brand-back { position: absolute; left: 395px; width: 300px; top: 296px; text-align: center; }
  .brand-back .wordmark { color: var(--paper); font-size: 25px; letter-spacing: 4px; }
  .brand-back .rule { background: var(--paper); margin-top: 12px; }
  .brand-back .tagline { color: var(--paper); margin-top: 12px; margin-left: -30px; }
</style>
</head>
<body>
  <section class="card card--front" aria-label="Visitkort forside">
    <div class="brand-front">
      <div class="brand-dot"></div>
      <div class="wordmark">lumavento</div>
      <div class="rule"></div>
      <div class="tagline">ideer med vind</div>
    </div>

    <div class="contact">
      <div class="contact__name">Marten Holmgaard</div>
      <div class="contact__role">Salgsdirektør</div>
      <address class="contact__address">Kastanjevej 14<br>8000 Aarhus C</address>
      <ul class="contact__list">
        <li class="contact__item">
          <svg class="contact__icon" viewBox="0 0 16 16"><path d="M3.6 1.2l2.3 2.4-1.3 2a9 9 0 0 0 5.8 5.8l2-1.3 2.4 2.3-1.6 2.3C6.6 14.6 1.4 9.4 1.3 2.8z"/></svg>
          +45 70 12 34 56
        </li>
        <li class="contact__item">
          <svg class="contact__icon" viewBox="0 0 16 16"><path d="M3.6 1.2l2.3 2.4-1.3 2a9 9 0 0 0 5.8 5.8l2-1.3 2.4 2.3-1.6 2.3C6.6 14.6 1.4 9.4 1.3 2.8z"/></svg>
          +45 60 98 76 54
        </li>
        <li class="contact__item">
          <svg class="contact__icon" viewBox="0 0 16 16"><path d="M1 3.5h14v9H1z M1.5 4l6.5 5 6.5-5" stroke="#fff" stroke-width="1.2"/></svg>
          mh@lumavento.dk
        </li>
        <li class="contact__item">
          <svg class="contact__icon" viewBox="0 0 16 16"><circle cx="8" cy="8" r="7"/><path d="M4 5c2 0 2 2 4 2s1 3 3 3M9 2.5c0 2 2 2 3.5 2" stroke="#fff" stroke-width="1.2" fill="none"/></svg>
          www.lumavento.dk
        </li>
      </ul>
    </div>

    <div class="stripes" aria-hidden="true">
      <div class="stripe--lime"></div>
      <div class="stripe--plum"></div>
      <div class="stripe--magenta"></div>
      <div class="stripe--tangerine"></div>
    </div>
  </section>

  <section class="card card--back" aria-label="Visitkort bagside">
    <div class="stripes" aria-hidden="true">
      <div class="stripe--lime"></div>
      <div class="stripe--plum"></div>
      <div class="stripe--magenta"></div>
      <div class="stripe--tangerine"></div>
    </div>
    <div class="brand-back">
      <div class="wordmark">lumavento</div>
      <div class="rule"></div>
      <div class="tagline">ideer med vind</div>
    </div>
  </section>
</body>
</html>
```